Commercial Post Cards

We are looking for 3 postcards that are similar but target 3 commercial property types. they will be 6x9 cards can be front and back or not.
1. Hotel Postcard – Taviqon / Bed Bug Protection
Use the attached Taviqon sample as the primary direction.
The focus should be:
Proactive bed bug prevention and control
Protecting guests and the hotel's reputation
Regular inspections
Documentation and risk management
Professional commercial pest management
The backside should transition into our General Pest Control services, showing that we can be the hotel's complete pest management provider beyond just bed bugs.
2. Apartment Complex Postcard
Target apartment owners, property managers, and management companies.
Focus on:
General pest control
Bed bug control
Rodent control
Preventative pest management
Protecting residents and the property
Reliable, ongoing service and documentation
The message should position us as a full-service pest management partner for multifamily properties.

3. Commercial Building Postcard
Target office buildings, banks, storage facilities, and other commercial properties.

Focus on:
General commercial pest control
Rodent control
Fly management
Recurring service programs
Protecting the property, employees, customers, and reputation

Overall Direction
All three postcards should have a consistent brand and visual style, but each should feel specifically designed for its target market.

We want the messaging to communicate:
Professional • Reliable • Proactive • Locally Owned & Operated • Serving Since 2017

The goal is not to overwhelm the reader with information. These should be marketing pieces that quickly communicate the problem we solve, our expertise, and why a commercial property should contact us.

I have included some of our marketing materials for help with what we do.

```html
<!DOCTYPE html>
<html lang="en">
<head>
<meta charset="utf-8">
<title>Veltrana Pest Control – Commercial Properties Guard</title>
<link rel="stylesheet" href="https://fonts.googleapis.com/css2?family=Bebas+Neue&family=Arimo:wght@700&display=swap">
<style>
  :root {
    --orange: #f58b46;
    --orange-deep: #f15a1f;
    --ink: #2a2a2a;
    --dark: #222325;
    --white: #ffffff;
    --sky: #5e9fe0;
    --glass: #7fb3d8;
    --lawn: #5c8a3a;
  }
  * { box-sizing: border-box; margin: 0; padding: 0; }
  html, body { width: 1200px; height: 800px; overflow: hidden; background: var(--white); }
  .card {
    position: relative; width: 1200px; height: 800px; overflow: hidden;
    background: var(--white); font-family: "Arimo", Arial, sans-serif; font-weight: 700; color: var(--ink);
  }
  .hero-photo {
    position: absolute; left: 420px; top: 0; width: 780px; height: 360px;
    background:
      linear-gradient(90deg, var(--white) 0%, rgba(255,255,255,0.6) 22%, rgba(255,255,255,0) 45%),
      linear-gradient(180deg, var(--sky) 0%, #bcd6ee 35%, var(--glass) 55%, #9fb7a0 80%, var(--lawn) 100%);
  }
  .brand {
    position: absolute; left: 40px; top: 62px;
    display: flex; align-items: center; gap: 12px;
  }
  .brand-mark { width: 34px; height: 34px; background: var(--orange-deep); }
  .brand-name { font-size: 36px; font-weight: 700; color: var(--ink); letter-spacing: -0.5px; }
  .headline {
    position: absolute; left: 37px; top: 150px;
    font-family: "Bebas Neue", "Oswald", sans-serif; font-weight: 400; font-size: 76px; line-height: 66px;
    color: var(--ink); letter-spacing: 0.3px;
  }
  .accent { color: var(--orange); }
  .subhead {
    position: absolute; left: 39px; top: 296px; font-size: 24px; line-height: 29px; color: var(--ink);
  }
  .promise-band {
    position: absolute; left: 0; top: 360px; width: 1200px; height: 52px;
    background: var(--orange); border-bottom: 6px solid var(--dark);
  }
  .promise-band p {
    position: absolute; left: 118px; top: 14px; font-size: 17px; color: var(--white); white-space: nowrap;
  }
  .band-shield { position: absolute; left: 38px; top: 346px; width: 72px; height: 80px; }
  .callout {
    position: absolute; left: 36px; top: 455px;
    font-family: "Bebas Neue", "Oswald", sans-serif; font-weight: 400; font-size: 98px; line-height: 88px;
    letter-spacing: -0.5px; color: var(--dark);
  }
  .services { position: absolute; top: 450px; list-style: none; }
  .services.col-a { left: 617px; width: 270px; }
  .services.col-b { left: 908px; width: 270px; }
  .services li {
    position: relative; padding-left: 43px; font-size: 20px; line-height: 25px; color: var(--ink);
    margin-bottom: 15px;
  }
  .services li svg { position: absolute; left: 0; top: 0; width: 24px; height: 27px; }
  .services.col-a li:first-child { margin-bottom: 17px; }
  .services.col-b li:first-child { margin-bottom: 17px; }
  .footer-band { position: absolute; left: 0; top: 683px; width: 1200px; height: 117px; background: var(--dark); }
  .quote-pill {
    position: absolute; left: 240px; top: 668px; width: 742px; height: 46px;
    background: var(--white); border: 4px solid var(--orange); border-radius: 0 23px 23px 0;
    overflow: hidden;
  }
  .quote-ask {
    position: absolute; left: 0; top: 0; height: 38px; width: 450px;
    background: var(--orange); clip-path: polygon(0 0, 430px 0, 450px 50%, 430px 100%, 0 100%);
    color: var(--white); font-size: 22px; line-height: 38px; padding-left: 56px; white-space: nowrap;
  }
  .quote-for {
    position: absolute; left: 458px; top: 0; line-height: 38px; font-size: 22px; color: var(--dark);
    white-space: nowrap;
  }
  .quote-shield { position: absolute; left: 218px; top: 646px; width: 76px; height: 84px; }
  .contact { position: absolute; top: 732px; left: 0; width: 1200px; height: 50px; color: var(--white); }
  .contact-item { position: absolute; top: 0; display: flex; align-items: center; gap: 20px; font-size: 32px; line-height: 46px; }
  .contact-item svg { width: 28px; height: 28px; }
  .contact-phone { left: 292px; }
  .contact-web { left: 640px; }
  .contact-divider { position: absolute; left: 598px; top: 0; width: 3px; height: 46px; background: var(--white); }
</style>
</head>
<body>
<main class="card">
  <div class="hero-photo" role="img" aria-label="Modern glass office building with landscaped lawn and trees under a blue sky"></div>

  <div class="brand">
    <span class="brand-mark"></span>
    <span class="brand-name">Veltrana Pest Control</span>
  </div>

  <h1 class="headline">Commercial<br>Properties <span class="accent">Guard</span></h1>
  <p class="subhead">Professional Pest Management<br>for Commercial Properties</p>

  <div class="promise-band">
    <p>Proactive protection. Quarterly inspected. Documented results. Peace of mind for your employees, customers, and business.</p>
  </div>
  <svg class="band-shield" viewBox="0 0 72 80" aria-hidden="true">
    <path d="M36 2 L70 12 V40 C70 60 54 72 36 78 C18 72 2 60 2 40 V12 Z" fill="var(--orange-deep)"/>
    <path d="M36 9 L63 17 V40 C63 56 50 66 36 71 C22 66 9 56 9 40 V17 Z" fill="var(--white)"/>
    <ellipse cx="36" cy="46" rx="10" ry="14" fill="var(--dark)"/>
    <circle cx="36" cy="28" r="5" fill="var(--dark)"/>
    <g stroke="var(--dark)" stroke-width="2" fill="none">
      <path d="M27 38 L18 32 M27 46 L17 46 M27 54 L18 60 M45 38 L54 32 M45 46 L55 46 M45 54 L54 60 M33 24 L28 18 M39 24 L44 18"/>
    </g>
  </svg>

  <h2 class="callout">Don’t let pests<br><span class="accent">Disrupt</span> Bussines</h2>

  <ul class="services col-a">
    <li><svg viewBox="0 0 24 27" aria-hidden="true"><path d="M12 1 L23 5 V13 C23 20 18 24 12 26 C6 24 1 20 1 13 V5 Z" fill="var(--orange)"/><path d="M12 4 L20 7 V13 C20 18 16 21 12 22.5 C8 21 4 18 4 13 V7 Z" fill="var(--dark)"/><path d="M8 13 L11 16 L16 10" stroke="var(--white)" stroke-width="2.4" fill="none"/></svg>General commercial pest control</li>
    <li><svg viewBox="0 0 24 27" aria-hidden="true"><path d="M12 1 L23 5 V13 C23 20 18 24 12 26 C6 24 1 20 1 13 V5 Z" fill="var(--orange)"/><path d="M12 4 L20 7 V13 C20 18 16 21 12 22.5 C8 21 4 18 4 13 V7 Z" fill="var(--dark)"/><path d="M8 13 L11 16 L16 10" stroke="var(--white)" stroke-width="2.4" fill="none"/></svg>Rodent control</li>
    <li><svg viewBox="0 0 24 27" aria-hidden="true"><path d="M12 1 L23 5 V13 C23 20 18 24 12 26 C6 24 1 20 1 13 V5 Z" fill="var(--orange)"/><path d="M12 4 L20 7 V13 C20 18 16 21 12 22.5 C8 21 4 18 4 13 V7 Z" fill="var(--dark)"/><path d="M8 13 L11 16 L16 10" stroke="var(--white)" stroke-width="2.4" fill="none"/></svg>Fly management</li>
    <li><svg viewBox="0 0 24 27" aria-hidden="true"><path d="M12 1 L23 5 V13 C23 20 18 24 12 26 C6 24 1 20 1 13 V5 Z" fill="var(--orange)"/><path d="M12 4 L20 7 V13 C20 18 16 21 12 22.5 C8 21 4 18 4 13 V7 Z" fill="var(--dark)"/><path d="M8 13 L11 16 L16 10" stroke="var(--white)" stroke-width="2.4" fill="none"/></svg>Preventative pest management</li>
  </ul>
  <ul class="services col-b">
    <li><svg viewBox="0 0 24 27" aria-hidden="true"><path d="M12 1 L23 5 V13 C23 20 18 24 12 26 C6 24 1 20 1 13 V5 Z" fill="var(--orange)"/><path d="M12 4 L20 7 V13 C20 18 16 21 12 22.5 C8 21 4 18 4 13 V7 Z" fill="var(--dark)"/><path d="M8 13 L11 16 L16 10" stroke="var(--white)" stroke-width="2.4" fill="none"/></svg>Recurring service programs</li>
    <li><svg viewBox="0 0 24 27" aria-hidden="true"><path d="M12 1 L23 5 V13 C23 20 18 24 12 26 C6 24 1 20 1 13 V5 Z" fill="var(--orange)"/><path d="M12 4 L20 7 V13 C20 18 16 21 12 22.5 C8 21 4 18 4 13 V7 Z" fill="var(--dark)"/><path d="M8 13 L11 16 L16 10" stroke="var(--white)" stroke-width="2.4" fill="none"/></svg>Protecting the<br>property, employees, customers, and reputation</li>
  </ul>

  <div class="footer-band"></div>
  <div class="quote-pill">
    <div class="quote-ask">ASK US FOR A CUSTOM QUOTE</div>
    <div class="quote-for">FOR YOUR PROPERTY.</div>
  </div>
  <svg class="quote-shield" viewBox="0 0 76 84" aria-hidden="true">
    <path d="M38 2 L74 13 V42 C74 63 57 76 38 82 C19 76 2 63 2 42 V13 Z" fill="var(--orange)"/>
    <path d="M38 9 L67 18 V42 C67 59 53 70 38 75 C23 70 9 59 9 42 V18 Z" fill="var(--dark)"/>
    <rect x="20" y="26" width="24" height="18" rx="4" fill="none" stroke="var(--white)" stroke-width="3"/>
    <rect x="32" y="36" width="24" height="18" rx="4" fill="var(--dark)" stroke="var(--white)" stroke-width="3"/>
    <text x="28" y="40" font-size="12" font-family="Arimo, sans-serif" font-weight="700" fill="var(--white)">?</text>
  </svg>

  <div class="contact">
    <div class="contact-item contact-phone">
      <svg viewBox="0 0 28 28" aria-hidden="true"><circle cx="14" cy="14" r="14" fill="var(--orange)"/><path d="M9 7 L12 7 L13 11 L11 12.5 C12 15 13 16 15.5 17 L17 15 L21 16 L21 19 C21 20 20 21 19 21 C13 21 7 15 7 9 C7 8 8 7 9 7 Z" fill="var(--white)"/></svg>
      <span>208-555-0142</span>
    </div>
    <div class="contact-divider"></div>
    <div class="contact-item contact-web">
      <svg viewBox="0 0 28 28" aria-hidden="true"><circle cx="14" cy="14" r="14" fill="var(--orange)"/><path d="M20 8 L7 13 L12 15 L14 20 Z" fill="var(--white)"/></svg>
      <span>www.veltranapest.com</span>
    </div>
  </div>
</main>
</body>
</html>
```